Horse Training Book Cover Design

We have had some book covers drafted by some freelancers on Gigtrove, but they just miss the mark a little bit.
This book is a Horse Training Book, but also entails a lot of mindfulness and attunement practices. Focus on effective Fonts.
We will be using Pellow Press. We want a paperback and hardback cover.
Specs: 5.50 x 8.50 inches
Pages: 250
I have uploaded the Gigtrove drafts as well as some drafts that I have made. We're looking for a tooled leather look, we want the title to look as if it was stamped into the leather background, but also make it easy to read the back print. I have attached multiple inspirations, but we don't just want you to use these, we want you to create something unique from them.
FRONT COVER TEXT
Title: The Foundations of Schooling
Subtitle: Understanding the relationship between you and your horse, and why effective training works.
Author: Dorian Halvey
BACK COVER TEXT
Quote: “As to methods there may be a million and then some, but Principles are few. The man who grasps principles can successfully select his own methods. The man who tries methods, ignoring principles, is sure to have trouble.” - Thaddeus Winlock Early 20th Century Efficiency Expert
Book Overview: In The Foundations of Schooling, Dorian Halvey describes the 12 principles that all successful horsemen and women use to effectively train horses. After 30 years of training, Dorian discovered a 13th principle that, when integrated with the others, makes you the best person to train your horse.
Book Review: “Dorian has a unique ability to understand both horse and rider from the inside out as he helps them individually - and together. Strong relationships come from trust and perceiving the other from their point of view. Horses do this naturally; fortunately for us, Dorian gives us humans the tools to understand ourselves and our horses.”
-Maribel Cronk, Rodeo Ranchwomen Gallery Inductee
Horse Owners
Education, Animals and Pets

```html
<!DOCTYPE html>
<html lang="en">
<head>
<meta charset="utf-8">
<title>The Foundations of Schooling – Cover Wrap</title>
<link rel="stylesheet" href="https://fonts.googleapis.com/css2?family=Open+Sans:ital,wght@0,400;0,600;0,700;0,800;1,500;1,600&display=swap">
<style>
  :root {
    --leather-dark: #5e2c12;
    --leather-mid: #7d4220;
    --leather-light: #935329;
    --stamp: #c99d8b;
    --stamp-shadow: rgba(40, 14, 4, 0.75);
    --frame: #b47d66;
    --ink-soft: #c89a86;
    --emboss: #7a3a22;
    --spine-white: #f4eee9;
  }
  * { margin: 0; padding: 0; box-sizing: border-box; }
  html, body { width: 1200px; height: 850px; overflow: hidden; background: var(--leather-dark); }
  .cover-wrap {
    position: relative; width: 1200px; height: 850px; overflow: hidden;
    font-family: "Open Sans", sans-serif;
    background:
      radial-gradient(ellipse at 30% 40%, rgba(170, 100, 50, 0.35), transparent 60%),
      radial-gradient(ellipse at 75% 65%, rgba(160, 90, 45, 0.3), transparent 55%),
      radial-gradient(ellipse at 50% 100%, rgba(40, 15, 5, 0.45), transparent 60%),
      linear-gradient(135deg, var(--leather-light), var(--leather-mid) 45%, var(--leather-dark));
  }
  .panel-frame {
    position: absolute; border: 2px solid var(--frame);
  }
  .panel-frame::after {
    content: ""; position: absolute; inset: 5px; border: 1px solid var(--frame); opacity: 0.8;
  }
  .back-frame { left: 27px; top: 23px; width: 503px; height: 804px; }
  .front-frame { left: 677px; top: 22px; width: 506px; height: 805px; }

  .divider { position: absolute; height: 16px; }
  .divider::before, .divider::after {
    content: ""; position: absolute; top: 8px; height: 1px; background: var(--frame); width: calc(50% - 36px);
  }
  .divider::before { left: 0; }
  .divider::after { right: 0; }
  .divider .ornament {
    position: absolute; left: 50%; top: 2px; width: 46px; height: 13px; margin-left: -23px;
    border-radius: 50%; background: var(--frame); opacity: 0.85;
  }
  .back-divider { left: 65px; width: 430px; }
  .front-divider { left: 715px; width: 430px; }

  .back-text {
    position: absolute; color: var(--ink-soft); font-style: italic; font-weight: 600;
    text-shadow: 0 1px 1px var(--stamp-shadow);
  }
  .quote { left: 70px; top: 80px; width: 430px; font-size: 17.4px; line-height: 21.7px; }
  .quote-source { left: 70px; top: 203px; font-size: 13.4px; }
  .overview { left: 203px; top: 266px; width: 295px; font-size: 17.2px; line-height: 21.6px; }
  .review { left: 68px; top: 548px; width: 430px; font-size: 17.2px; line-height: 21.7px; }
  .review-source { left: 68px; top: 733px; font-size: 14px; }

  .emblem {
    position: absolute; border-radius: 40% 55% 45% 50%;
    background: radial-gradient(ellipse at 40% 40%, #8a4327, var(--emboss));
    box-shadow: inset 2px 2px 3px rgba(30, 10, 3, 0.6), 1px 1px 0 rgba(210, 150, 120, 0.35);
  }
  .emblem-back { left: 72px; top: 262px; width: 100px; height: 84px; }
  .emblem-front { left: 822px; top: 55px; width: 208px; height: 175px; }

  .spine-title {
    position: absolute; left: 583px; top: 40px; width: 36px; height: 676px;
    writing-mode: vertical-rl; transform: rotate(180deg);
    color: var(--spine-white); font-weight: 600; font-size: 24px; letter-spacing: 1.6px;
    white-space: nowrap; text-align: left; line-height: 36px;
  }
  .spine-mark {
    position: absolute; left: 576px; top: 750px; width: 58px; height: 66px;
    border-radius: 45% 50% 30% 40%; background: var(--spine-white); opacity: 0.92;
  }

  .front-title {
    position: absolute; left: 690px; top: 238px; width: 480px; text-align: center;
    color: var(--stamp); font-weight: 800; font-size: 74px; line-height: 80px; letter-spacing: -0.5px;
    text-shadow: 2px 3px 3px var(--stamp-shadow), -1px -1px 0 rgba(255, 220, 200, 0.25);
  }
  .front-title span { display: block; }
  .subtitle {
    position: absolute; left: 700px; top: 542px; width: 460px; text-align: center;
    color: var(--stamp); font-weight: 600; font-size: 26.5px; line-height: 34.5px;
    text-shadow: 1px 2px 2px var(--stamp-shadow);
  }
  .author {
    position: absolute; left: 690px; top: 722px; width: 480px; text-align: center;
    color: var(--stamp); font-weight: 600; font-size: 34px;
    text-shadow: 1px 2px 2px var(--stamp-shadow);
  }
</style>
</head>
<body>
<main class="cover-wrap">
  <section class="back-cover" aria-label="Back cover">
    <div class="panel-frame back-frame"></div>
    <div class="divider back-divider" style="top:52px"><span class="ornament" role="img" aria-label="Flourish ornament"></span></div>
    <p class="back-text quote">“As to methods there may be a million and then some, but Principles are few. The man who grasps principles can successfully select his own methods. The man who tries methods, ignoring principles, is sure to have trouble.”</p>
    <p class="back-text quote-source">((Thaddeus Winlock Early 20th Century Efficiency Expert))</p>
    <div class="divider back-divider" style="top:235px"><span class="ornament" role="img" aria-label="Flourish ornament"></span></div>
    <div class="emblem emblem-back" role="img" aria-label="Embossed horse head emblem"></div>
    <p class="back-text overview">In The Foundations of Schooling, Dorian Halvey describes the 12 principles that all successful horsemen and women use to effectively train horses. After 30 years of training, Dorian discovered a 13th principle that, when integrated with the others, makes you the best person to train your horse.</p>
    <div class="divider back-divider" style="top:514px"><span class="ornament" role="img" aria-label="Flourish ornament"></span></div>
    <p class="back-text review">Book Review: “Dorian has a unique ability to understand both horse and rider from the inside out as he helps them individually - and together. Strong relationships come from trust and perceiving the other from their point of view. Horses do this naturally; fortunately for us, Dorian gives us humans the tools to understand ourselves and our horses.”</p>
    <p class="back-text review-source">(Maribel Cronk, Rodeo Ranchwomen Gallery Inductee)</p>
    <div class="divider back-divider" style="top:775px"><span class="ornament" role="img" aria-label="Flourish ornament"></span></div>
  </section>

  <section class="spine" aria-label="Spine">
    <p class="spine-title">The Foundations of Schooling | Dorian Halvey</p>
    <div class="spine-mark" role="img" aria-label="Small horse emblem"></div>
  </section>

  <section class="front-cover" aria-label="Front cover">
    <div class="panel-frame front-frame"></div>
    <div class="emblem emblem-front" role="img" aria-label="Embossed horse head emblem"></div>
    <h1 class="front-title"><span>The</span><span>Foundations</span><span>of Schooling</span></h1>
    <div class="divider front-divider" style="top:515px"><span class="ornament" role="img" aria-label="Flourish ornament"></span></div>
    <p class="subtitle">Understanding the relationship between you and your horse, and why effective training works.</p>
    <div class="divider front-divider" style="top:689px"><span class="ornament" role="img" aria-label="Flourish ornament"></span></div>
    <p class="author">Dorian Halvey</p>
  </section>
</main>
</body>
</html>
```